Business Card Design

Hi I need a business card designed, we already have the business name logo artwork and would like some concept ideas for the Bus Card layout.
On the back of the card i want to include the products and services that we offer.
We are a Plastics Sheeting manufacture based in Perth Australia.

                                       

We need a BC design for a company called Tarvo Plastics based in Perth Australia.

We supply from DIY to Trade & Industrial  Engineering Markets.

We specialise in:

·         Cut to size panels  (all shapes and sizes)

·         Plastics fabrication & Welding

·         Custom Designs

·         Plastic Repairs

·         PVC Pipe Slotting & PVC Pipe Threading

·         Supplier of all types of engineering plastics and profiles.

Including:           Acrylic / Clarvene

                               Polycarbonate / Dorvil

                               Prismatic Light Diffuser

                               Vantrib

                               HDPE / UHMWPE

                               PVC / PVC Foam

                               Nylon

                               HIPS

```html
<!DOCTYPE html>
<html lang="en">
<head>
<meta charset="utf-8">
<title>Tarvo Plastics – Business Card</title>
<link href="https://fonts.googleapis.com/css2?family=Open+Sans:wght@400;600;700;800&display=swap" rel="stylesheet">
<style>
  :root {
    --navy: #1e2b5e;
    --navy-text: #22306a;
    --orange: #f2a31b;
    --white: #ffffff;
    --grey-text: #3b3b3b;
    --backdrop: #e9e7e3;
    --divider: #8d95b5;
  }
  * { box-sizing: border-box; margin: 0; padding: 0; }
  html, body { width: 1200px; height: 720px; overflow: hidden; }
  body {
    background: var(--backdrop);
    font-family: "Open Sans", Arial, sans-serif;
    display: flex;
    align-items: center;
    justify-content: center;
    gap: 40px;
  }
  .card {
    width: 540px;
    height: 309px;
    position: relative;
    overflow: hidden;
    box-shadow: 0 6px 18px rgba(0,0,0,0.18);
  }

  /* Front */
  .card-front { background: var(--navy); }
  .front-top {
    position: absolute; left: 0; top: 0; right: 0; height: 150px;
    background: var(--white);
  }
  .front-brand {
    position: absolute; left: 48px; top: 26px;
    display: flex; align-items: center; gap: 12px;
  }
  .brand-mark { width: 22px; height: 22px; background: var(--orange); }
  .brand-name {
    font-weight: 800; font-size: 44px; letter-spacing: -0.5px;
    color: var(--navy-text); line-height: 1;
  }
  .front-address {
    position: absolute; right: 40px; top: 94px;
    text-align: right; color: var(--grey-text);
    font-size: 12.5px; line-height: 18px;
  }
  .front-details {
    position: absolute; left: 30px; top: 166px; color: var(--white);
  }
  .person-name { font-size: 17px; font-weight: 700; }
  .person-name .title { font-size: 12px; font-weight: 400; }
  .contact-row {
    display: flex; align-items: center; gap: 18px;
    font-size: 13px; margin-top: 6px;
  }
  .contact-item { display: flex; align-items: center; gap: 6px; }
  .contact-item svg { width: 13px; height: 13px; fill: var(--white); }
  .trading-name { font-size: 11.5px; margin-top: 8px; padding-left: 19px; }

  /* Back */
  .card-back { background: var(--navy); color: var(--white); }
  .back-brand {
    position: absolute; left: 0; right: 0; top: 18px;
    display: flex; justify-content: center; align-items: center; gap: 12px;
  }
  .card-back .brand-name { color: var(--white); font-size: 40px; }
  .back-intro {
    position: absolute; left: 0; right: 0; top: 76px;
    text-align: center; font-size: 13.5px; font-weight: 700; line-height: 18px;
  }
  .offer-column { position: absolute; top: 124px; }
  .offer-column.services { left: 30px; width: 290px; }
  .offer-column.materials { left: 352px; width: 170px; }
  .column-heading {
    color: var(--orange); font-size: 16px; font-weight: 700; margin-bottom: 4px;
  }
  .offer-list { list-style: none; font-size: 12.5px; line-height: 17px; }
  .offer-list li { position: relative; padding-left: 12px; }
  .offer-list li::before {
    content: ""; position: absolute; left: 0; top: 6px;
    width: 6px; height: 6px; border-radius: 50%; background: var(--orange);
  }
  .offer-list .pair { display: flex; gap: 12px; }
  .offer-list .pair span { position: relative; }
  .offer-list .pair span + span { padding-left: 12px; }
  .offer-list .pair span + span::before {
    content: ""; position: absolute; left: 0; top: 6px;
    width: 6px; height: 6px; border-radius: 50%; background: var(--orange);
  }
  .column-divider {
    position: absolute; left: 334px; top: 128px; width: 1px; height: 150px;
    background: var(--divider);
  }
</style>
</head>
<body>

  <section class="card card-front">
    <div class="front-top">
      <div class="front-brand">
        <span class="brand-mark"></span>
        <span class="brand-name">Tarvo Plastics</span>
      </div>
      <div class="front-address">
        <p>Unit 4/18 Harlow Circuit Brenmore WA 6155</p>
        <p>PO Box 2240 Brenmore DC WA 6970</p>
      </div>
    </div>
    <div class="front-details">
      <p class="person-name">Your Name, <span class="title">Title</span></p>
      <div class="contact-row">
        <span class="contact-item">
          <svg viewBox="0 0 24 24"><path d="M6.6 10.8a15.1 15.1 0 0 0 6.6 6.6l2.2-2.2a1 1 0 0 1 1-.25 11.4 11.4 0 0 0 3.6.57 1 1 0 0 1 1 1V20a1 1 0 0 1-1 1A17 17 0 0 1 3 4a1 1 0 0 1 1-1h3.5a1 1 0 0 1 1 1c0 1.25.2 2.45.57 3.6a1 1 0 0 1-.25 1z"/></svg>
          08 9471 3056
        </span>
        <span class="contact-item">
          <svg viewBox="0 0 24 24"><path d="M6 8h12v10H6z M8 3h8v5H8z M8 11h2v2H8z M11 11h2v2h-2z M14 11h2v2h-2z M8 14h8v2H8z"/></svg>
          08 9471 3057
        </span>
      </div>
      <div class="contact-row">
        <span class="contact-item">
          <svg viewBox="0 0 24 24"><path d="M8 1h8a2 2 0 0 1 2 2v18a2 2 0 0 1-2 2H8a2 2 0 0 1-2-2V3a2 2 0 0 1 2-2zm0 3v14h8V4z"/></svg>
          123-456-7890
        </span>
      </div>
      <div class="contact-row">
        <span class="contact-item">
          <svg viewBox="0 0 24 24"><path d="M2 5h20v14H2z M3.5 6.5 12 13l8.5-6.5" stroke="#1e2b5e" stroke-width="1.6"/></svg>
          sales@tarvoplastics.com.au
        </span>
      </div>
      <p class="trading-name">Kestrel Holdings Pty Ltd T/A Tarvo Plastics ABN: TBA</p>
    </div>
  </section>

  <section class="card card-back">
    <div class="back-brand">
      <span class="brand-mark"></span>
      <span class="brand-name">Tarvo Plastics</span>
    </div>
    <div class="back-intro">
      <p>The Products And Services That We Offer</p>
      <p>Are Supplied From Diy To Trade &amp; Industrial Engineering Markets</p>
    </div>

    <div class="offer-column services">
      <h2 class="column-heading">We specialise in:</h2>
      <ul class="offer-list">
        <li>Cut to size panels (all shapes and sizes)</li>
        <li>Plastics fabrication &amp; Welding</li>
        <li>Custom Designs</li>
        <li>Plastic Repairs</li>
        <li>PVC Pipe Slotting &amp; PVC Pipe Threading</li>
        <li>Supplier of all types of engineering plastics and profiles</li>
      </ul>
    </div>

    <div class="column-divider"></div>

    <div class="offer-column materials">
      <h2 class="column-heading">Including:</h2>
      <ul class="offer-list">
        <li>Acrylic / Clarvene</li>
        <li>Polycarbonate / Dorvil</li>
        <li>Prismatic Light Diffuser</li>
        <li class="pair"><span>Vantrib</span><span>HDPE / UHMWPE</span></li>
        <li>PVC / PVC Foam</li>
        <li class="pair"><span>Nylon</span><span>HIPS</span></li>
      </ul>
    </div>
  </section>

</body>
</html>
```